Investigation Before Elimination

Create a very professional and eye-catching Infographic for Birch Supply that is intended to convey to retailers that they should investigate why products are NOT selling in the Birch Supply store before they apply a discount to get rid of it. The infographic should capture all of the questions they should think about before making cutting the price. See the attachment for details on wording.

Target Market(s)

Birch Supply Business Owners

Industry/Entity Type

Retail

Font styles to use
Sans Serif

Requirements
Must have
• Any product in the infographic must be home improvement related product. See our website for ideas:
https://www.birchsupply.example/?utm_source=google&utm_medium=cpc&gclid=QxwPLMnt4R2FTkBkLpwD8WXYM5n_qa3HTkvb9aJ742_9Rm-dpLzk9Tnm80vt5zXrJg0b6-Ydxk7-vNZPm-kqEtnPAwD_BwE&gclsrc=aw.ds

* Must be in Birch Supply related colors
* Must be fun, exciting, eye-catching, unique, and clever
* 1-Page preferable but no more than two standard 8-1/2"x11"
* See the attachment for details on wording.
Should not have
• N/A

```html
<!DOCTYPE html>
<html lang="en">
<head>
<meta charset="utf-8">
<title>Investigation Before Elimination – Birch Supply</title>
<link rel="stylesheet" href="https://fonts.googleapis.com/css2?family=Roboto+Slab:wght@800&family=Roboto:wght@300;400;500;700&family=Roboto+Condensed:wght@700&display=swap">
<style>
:root{
  --ink:#3a3a3a;
  --text:#2b2b2b;
  --red:#e31b37;
  --c1:#b01f24; --c1-pale:#efc9c6;
  --c2:#e31b37; --c2-pale:#f8d0d5;
  --c3:#e8892b; --c3-pale:#fbe1c8;
  --c4:#f2e43f; --c4-pale:#fcf8d0;
  --c5:#7cc242; --c5-pale:#deedd0;
  --c6:#7ab8e0; --c6-pale:#dbeaf5;
  --c7:#9b6aa0; --c7-pale:#e4d9e6;
  --c8:#e91e7b; --c8-pale:#f9d0e2;
  --core:#3d3d3d;
  --footer:#e6e6e6;
  --bar:#8a8888;
}
*{margin:0;padding:0;box-sizing:border-box}
html,body{width:1200px;height:750px;overflow:hidden;background:#fff}
body{font-family:"Roboto",Arial,sans-serif;color:var(--text)}
.canvas{position:relative;width:1200px;height:750px;overflow:hidden;background:#fff}

.title{position:absolute;left:34px;top:22px;font-family:"Roboto Slab",Georgia,serif;font-weight:800;font-size:66px;line-height:80px;letter-spacing:-1px;white-space:nowrap;color:var(--ink)}
.title .before{display:inline-block;background:var(--ink);color:#fff;font-size:30px;line-height:38px;padding:0 10px;vertical-align:14px;margin:0 10px 0 12px;letter-spacing:0}
.title .elim{color:var(--red)}
.title-rule{position:absolute;left:34px;top:103px;width:982px;height:1px;background:#bdbdbd}

.brand{position:absolute;left:1030px;top:50px;display:flex;align-items:center;gap:8px}
.brand .mark{width:18px;height:18px;background:var(--red)}
.brand .name{font-family:"Roboto",Arial,sans-serif;font-weight:700;font-size:22px;color:var(--red);white-space:nowrap}

.lead{position:absolute;left:30px;width:1140px;text-align:center}
.lead.strong{top:119px;font-weight:700;font-size:15.4px;line-height:19px;color:#333}
.lead.soft{top:164px;font-weight:400;font-size:15.2px;line-height:19.5px;color:#444}

.footer{position:absolute;left:0;top:573px;width:1200px;height:127px;background:var(--footer)}
.resources{position:absolute;left:0;top:590px;width:1200px;text-align:center}
.resources .intro{font-size:15.5px;color:#3d3d3d;margin-bottom:4px}
.resources .link{display:block;font-size:14px;line-height:24px;color:var(--red);text-decoration:none;font-weight:500}
.resources .link sup{font-size:8px;font-style:italic;font-weight:700}
.contact-bar{position:absolute;left:0;top:700px;width:1200px;height:50px;background:var(--bar);color:#fff;display:flex;align-items:center;justify-content:center;gap:10px;font-size:13px}
.contact-bar svg{width:16px;height:16px}
.contact-bar .item{display:flex;align-items:center;gap:5px}

.wheel{position:absolute;left:0;top:0}

.core-text{position:absolute;left:440px;top:440px;width:320px;text-align:center;color:#fff;font-weight:300;font-size:19.5px;line-height:22.6px}
.core-text .yes{display:inline-block;background:var(--red);font-weight:700;padding:0 6px;line-height:21px}

.num{position:absolute;font-family:"Roboto Condensed","Arial Narrow",sans-serif;font-weight:700;font-size:39px;line-height:40px}
.q{position:absolute;width:240px}
.q.left{text-align:right}
.q h3{font-size:11.4px;line-height:15px;font-weight:700}
.q p{font-size:10.2px;line-height:12.8px;color:#333;margin-top:4px}

.n1,.q1 h3{color:var(--c1)}
.n2,.q2 h3{color:var(--c2)}
.n3,.q3 h3{color:var(--c3)}
.n4{color:var(--c4)}
.q4 h3{color:#2b2b2b}
.n5,.q5 h3{color:var(--c5)}
.n6,.q6 h3{color:var(--c6)}
.n7,.q7 h3{color:var(--c7)}
.n8,.q8 h3{color:var(--c8)}
</style>
</head>
<body>
<div class="canvas">

  <h1 class="title">Investigation<span class="before">BEFORE</span><span class="elim">Elimination</span></h1>
  <div class="title-rule"></div>

  <div class="brand"><span class="mark"></span><span class="name">Birch Supply</span></div>

  <p class="lead strong">Dead stock in your store rapidly eats away at profits, drives up the cost of doing business, and occupies valuable shelf space that would be better served by fresh and more productive products. To address this issue, a typical knee-jerk response is marking down the product and attempting to sell it at a discount.</p>
  <p class="lead soft">Though this is a better approach than simply hoping it sells ‘one day’, applying a markdown should be used only as a last resort after sales floor investigation takes place for common execution issues that are known to hamper sales;</p>

  <div class="footer"></div>

  <svg class="wheel" width="1200" height="750" viewBox="0 0 1200 750" aria-hidden="true">
    <g class="segments">
      <path fill="var(--c1)" d="M600 573 L329 573 A271 271 0 0 1 349.6 469.3 Z"/>
      <path fill="var(--c2)" d="M600 573 L349.6 469.3 A271 271 0 0 1 408.4 381.4 Z"/>
      <path fill="var(--c3)" d="M600 573 L408.4 381.4 A271 271 0 0 1 496.3 322.6 Z"/>
      <path fill="var(--c4)" d="M600 573 L496.3 322.6 A271 271 0 0 1 600 302 Z"/>
      <path fill="var(--c5)" d="M600 573 L600 302 A271 271 0 0 1 703.7 322.6 Z"/>
      <path fill="var(--c6)" d="M600 573 L703.7 322.6 A271 271 0 0 1 791.6 381.4 Z"/>
      <path fill="var(--c7)" d="M600 573 L791.6 381.4 A271 271 0 0 1 850.4 469.3 Z"/>
      <path fill="var(--c8)" d="M600 573 L850.4 469.3 A271 271 0 0 1 871 573 Z"/>
    </g>
    <g class="inner-ring">
      <path fill="var(--c1-pale)" d="M600 573 L389 573 A211 211 0 0 1 405.1 492.3 Z"/>
      <path fill="var(--c2-pale)" d="M600 573 L405.1 492.3 A211 211 0 0 1 450.8 423.8 Z"/>
      <path fill="var(--c3-pale)" d="M600 573 L450.8 423.8 A211 211 0 0 1 519.3 378.1 Z"/>
      <path fill="var(--c4-pale)" d="M600 573 L519.3 378.1 A211 211 0 0 1 600 362 Z"/>
      <path fill="var(--c5-pale)" d="M600 573 L600 362 A211 211 0 0 1 680.7 378.1 Z"/>
      <path fill="var(--c6-pale)" d="M600 573 L680.7 378.1 A211 211 0 0 1 749.2 423.8 Z"/>
      <path fill="var(--c7-pale)" d="M600 573 L749.2 423.8 A211 211 0 0 1 794.9 492.3 Z"/>
      <path fill="var(--c8-pale)" d="M600 573 L794.9 492.3 A211 211 0 0 1 811 573 Z"/>
    </g>
    <path class="core" fill="var(--core)" d="M424 573 A176 176 0 0 1 776 573 Z"/>

    <g class="icons" fill="none" stroke="#fff" stroke-width="2" stroke-linejoin="round" stroke-linecap="round">
      <!-- open box -->
      <g transform="translate(364 526)">
        <path d="M-12 -4 L0 -10 L12 -4 L0 2 Z M-12 -4 V8 L0 14 L12 8 V-4 M0 2 V14 M-12 -4 L-16 -10 L-4 -16 L0 -10 M12 -4 L16 -10 L4 -16 L0 -10"/>
      </g>
      <!-- shelving -->
      <g transform="translate(400 439)">
        <path d="M-14 -12 H14 V14 H-14 Z M-14 -3 H14 M-14 6 H14 M-10 -12 V-17 M-5 -12 V-17 M0 -12 V-17 M5 -12 V-17 M10 -12 V-17"/>
        <circle cx="-8" cy="10" r="2.5"/><circle cx="0" cy="10" r="2.5"/><circle cx="8" cy="10" r="2.5"/>
      </g>
      <!-- price tag -->
      <g transform="translate(466 373) rotate(-40)">
        <path d="M-16 -9 H8 L16 0 L8 9 H-16 Z"/>
        <circle cx="9" cy="0" r="2"/>
        <path d="M-5 -5 V5 M-2 -3 Q-5 -5 -8 -3 Q-8 0 -5 0 Q-2 0 -2 3 Q-5 5 -8 3"/>
      </g>
      <!-- box with idea -->
      <g transform="translate(553 337)">
        <path d="M-12 0 L0 -5 L12 0 L0 5 Z M-12 0 V11 L0 16 L12 11 V0 M0 5 V16"/>
        <circle cx="0" cy="-11" r="5"/>
        <path d="M0 -19 V-21 M-8 -13 L-10 -14 M8 -13 L10 -14"/>
      </g>
      <!-- scanner frame with magnifier -->
      <g transform="translate(647 337)">
        <path d="M-16 -10 V-15 H-11 M11 -15 H16 V-10 M16 10 V15 H11 M-11 15 H-16 V10"/>
        <path d="M-9 -9 V9 M-5 -9 V9 M-1 -9 V2"/>
        <circle cx="6" cy="3" r="5"/>
        <path d="M10 7 L14 11"/>
      </g>
      <!-- cart -->
      <g transform="translate(734 373)">
        <path d="M-17 -13 H-12 L-8 7 H12 L15 -7 H-10"/>
        <path d="M-8 -1 H13 M-3 -7 V7 M3 -7 V7 M8 -7 V7"/>
        <circle cx="-6" cy="12" r="2.5"/><circle cx="10" cy="12" r="2.5"/>
      </g>
      <!-- basket with minus -->
      <g transform="translate(800 439)">
        <path d="M-15 -4 H15 L12 13 H-12 Z M-9 -4 L-3 -15 M9 -4 L3 -15"/>
        <path d="M-6 2 V8 M0 2 V8"/>
        <circle cx="10" cy="9" r="6" fill="var(--c7)"/>
        <path d="M7 9 H13"/>
      </g>
      <!-- sale tag -->
      <g transform="translate(836 526) rotate(-12)">
        <path d="M-11 -10 L0 -16 L11 -10 V16 H-11 Z"/>
        <circle cx="0" cy="-9" r="2"/>
        <path d="M-7 0 H7 M-7 6 H7"/>
      </g>
    </g>

    <g class="connectors" fill="none" stroke-width="1">
      <path stroke="var(--c1)" d="M299 508 H329"/>
      <path stroke="var(--c2)" d="M320 418 H338 L358 430"/>
      <path stroke="var(--c3)" d="M376 333 H398 L430 353"/>
      <path stroke="var(--c4)" d="M503 245 H532 L547 301"/>
      <path stroke="var(--c5)" d="M696 245 H664 L647 301"/>
      <path stroke="var(--c6)" d="M818 333 H790 L765 354"/>
      <path stroke="var(--c7)" d="M875 419 H856 L834 430"/>
      <path stroke="var(--c8)" d="M902 508 H872"/>
    </g>
  </svg>

  <p class="core-text">It is only after<br>saying <span class="yes">“YES”</span> to these<br>questions should an item<br>be considered for a markdown<br>strategy</p>

  <span class="num n1" style="left:257px;top:488px">01</span>
  <span class="num n2" style="left:268px;top:400px">02</span>
  <span class="num n3" style="left:327px;top:312px">03</span>
  <span class="num n4" style="left:450px;top:224px">04</span>
  <span class="num n5" style="left:707px;top:224px">05</span>
  <span class="num n6" style="left:832px;top:312px">06</span>
  <span class="num n7" style="left:888px;top:400px">07</span>
  <span class="num n8" style="left:914px;top:488px">08</span>

  <div class="q q1 left" style="right:964px;top:492px">
    <h3>Is the product physically there?</h3>
    <p>One of the most typical issues is that<br>the item is no longer existent (i.e.<br>ghost inventory).</p>
  </div>
  <div class="q q2 left" style="right:946px;top:403px">
    <h3>Is the item merchandised properly -<br>Is it in plain view of the customer?</h3>
    <p>Find out if it is stuck in the backroom, top<br>stock, or buried behind other products.</p>
  </div>
  <div class="q q3 left" style="right:889px;top:315px">
    <h3>Is the item priced competitively?</h3>
    <p>In today’s price sensitive market, making<br>sure the cost of the SKU is in line with<br>the customer expectation is key.</p>
  </div>
  <div class="q q4 left" style="right:770px;top:226px">
    <h3>Is the physical product and<br>packaging in a desirable condition?</h3>
    <p>Bottom-line: Nobody wants ripped or torn,<br>or physically abused merchandise.</p>
  </div>
  <div class="q q5" style="left:762px;top:226px;width:270px">
    <h3>Is the item unique enough to where an alike<br>SKU isn’t cannibalizing its sales?</h3>
    <p>Each SKU needs to be different and stand on its own.<br>Eliminate redundancies in the product mix.</p>
  </div>
  <div class="q q6" style="left:886px;top:315px;width:260px">
    <h3>Do you have enough quantity of the item for<br>the customer to want to make the purchase?</h3>
    <p>Seldom do consumers come in to buy one or two<br>casters (i.e. project SKU). Having sufficient quantity<br>to sell the job quantity is key</p>
  </div>
  <div class="q q7" style="left:943px;top:403px;width:240px">
    <h3>Is the item still relevant to the shopper?</h3>
    <p>Get rid of outdated product and technology…<br>those old rotary dial phone cords!</p>
  </div>
  <div class="q q8" style="left:967px;top:492px;width:220px">
    <h3>Is the sale of the SKU independent<br>of the sale of another item?</h3>
    <p>With SKUs that depend on each other<br>to sell, analyze the sell through and<br>performance of the other item.</p>
  </div>

  <div class="resources">
    <p class="intro">For further detail on in-stock position, see the following resources (click to visit link):</p>
    <a class="link" href="#">Obsolete Inventory - Closeout Management (COM) Setup <sup>(URL)</sup></a>
    <a class="link" href="#">In-Stock Procedures <sup>(URL)</sup></a>
    <a class="link" href="#">Markdown Strategy <sup>(URL)</sup></a>
  </div>

  <div class="contact-bar">
    <span>For more information, contact Store Systems and Operations:</span>
    <span class="item">
      <svg viewBox="0 0 16 16" fill="none" stroke="#fff" stroke-width="1.2" aria-hidden="true"><circle cx="8" cy="8" r="7.2"/><path d="M5.2 4 L6.6 4 L7.2 6 L6.3 6.8 Q7 8.6 9 9.6 L9.9 8.8 L11.9 9.4 V10.8 Q11 12 9.6 11.7 Q5.2 10.4 4.3 6 Q4.1 4.6 5.2 4 Z" fill="#fff" stroke="none"/></svg>
      555.014.2290
    </span>
    <span class="item">
      <svg viewBox="0 0 16 16" fill="none" stroke="#fff" stroke-width="1.2" aria-hidden="true"><rect x="1" y="3.5" width="14" height="9"/><path d="M1 3.5 L8 9 L15 3.5 M1 12.5 L6 7.6 M15 12.5 L10 7.6"/></svg>
      storeoperations@birchsupply.example
    </span>
  </div>

</div>
</body>
</html>
```